4th Generation Family Business Needs a New Card Design!

We are a family owned 4th Generation company. We are based in the Sydney, Australia area and we are desperately in need of a more modern and classy card. We are monumental masons who design, supply & erect lasting memorials throughout cemeteries in Sydney. Our customers are normally in a period of grieving. I have attached logo files that will need to be implemented on the card. Company was established 1935. Australian Owned and Operated. Card needs to be designed to PIXO.com specification.

Target Market(s)

Our target market is based upon people that a grieving for family members that have passed away. We also deal with alot of companies that own and operate cemeteries.

Industry/Entity Type

Business

Contact Information for Business Card

Simon Harcourt, Operations Manager, 0417293086, simon@harcourtmemorials.com.au
Lewis Harcourt, Director, 0491630572, lewis@harcourtmemorials.com.au
Phone # 02 9561 3048
Website: www.harcourtmemorials.com.au
Address: Suite 17, 8 Palfrey Lane, West Carlow, Sydney NSW 2156

Font styles to use
Serif
Decorative
Script

Requirements
Must have
• Would like to see the logo nicely implemented with a modern design. Embossed lettering would be a nice additive.

```html
<!DOCTYPE html>
<html lang="en">
<head>
<meta charset="utf-8">
<title>Harcourt Memorials — Business Card</title>
<link rel="stylesheet" href="https://fonts.googleapis.com/css2?family=Cinzel:wght@400;600&family=Open+Sans:wght@400&display=swap">
<style>
  :root {
    --bg: #8a8a8a;
    --card-dark: #1f1d1d;
    --band-dark: #231f20;
    --gold: #e8b92c;
    --white: #ffffff;
    --ink: #3a3a3a;
    --muted: #555555;
  }
  * { margin: 0; padding: 0; box-sizing: border-box; }
  html, body { width: 1200px; height: 950px; overflow: hidden; }
  body {
    background: radial-gradient(circle at 50% 45%, #a9a9a9 0%, var(--bg) 60%, #6e6e6e 100%);
    position: relative;
    font-family: "Open Sans", Arial, sans-serif;
  }
  .card {
    position: absolute;
    left: 250px;
    width: 700px;
    height: 400px;
    overflow: hidden;
    box-shadow: 0 8px 24px rgba(0,0,0,0.35);
  }
  /* Front */
  .card-front { top: 50px; background: var(--card-dark); }
  .front-brand {
    position: absolute; left: 0; right: 0; top: 130px;
    display: flex; align-items: center; justify-content: center; gap: 14px;
  }
  .brand-square {
    width: 34px; height: 34px; background: var(--gold);
  }
  .front-brand .brand-name {
    font-family: "Cinzel", Georgia, serif; font-weight: 600;
    font-size: 40px; letter-spacing: 2px; color: var(--white);
  }
  .front-web {
    position: absolute; left: 0; right: 0; top: 262px; text-align: center;
    color: var(--white); font-size: 17px; letter-spacing: 0.3px;
  }
  /* Back */
  .card-back { top: 500px; background: var(--white); }
  .gold-band {
    position: absolute; left: 470px; top: 20px; width: 230px; height: 56px;
    background: var(--gold);
  }
  .dark-band {
    position: absolute; left: 0; top: 76px; width: 470px; height: 120px;
    background: var(--band-dark);
  }
  .identity {
    position: absolute; left: 48px; top: 112px;
    font-family: "Cinzel", Georgia, serif;
  }
  .identity .person {
    color: var(--white); font-weight: 600; font-size: 27px; letter-spacing: 1px; line-height: 1.1;
  }
  .identity .role {
    color: var(--gold); font-size: 19px; letter-spacing: 1px; margin-top: 2px;
  }
  .back-brand {
    position: absolute; left: 486px; top: 92px; width: 200px;
    display: flex; align-items: center; gap: 10px;
  }
  .back-brand .brand-square { width: 22px; height: 22px; flex: none; }
  .back-brand .brand-name {
    font-family: "Cinzel", Georgia, serif; font-weight: 600;
    font-size: 22px; line-height: 1.1; color: var(--band-dark); letter-spacing: 1px;
  }
  .address {
    position: absolute; right: 40px; top: 168px; text-align: right;
    font-style: normal; color: var(--muted); font-size: 16px; line-height: 1.55;
  }
  .contacts {
    position: absolute; left: 44px; top: 270px; list-style: none;
    color: var(--ink); font-size: 16px; line-height: 1.55;
  }
  .contacts li { display: flex; align-items: center; gap: 10px; }
  .contacts svg { width: 14px; height: 14px; flex: none; fill: var(--band-dark); }
</style>
</head>
<body>

<section class="card card-front" aria-label="Card front">
  <div class="front-brand">
    <span class="brand-square"></span>
    <span class="brand-name">HARCOURT MEMORIALS</span>
  </div>
  <p class="front-web">www.harcourtmemorials.com.au</p>
</section>

<section class="card card-back" aria-label="Card back">
  <div class="gold-band"></div>
  <div class="dark-band"></div>

  <div class="identity">
    <p class="person">Simon Harcourt</p>
    <p class="role">Operations Manager</p>
  </div>

  <div class="back-brand">
    <span class="brand-square"></span>
    <span class="brand-name">HARCOURT MEMORIALS</span>
  </div>

  <address class="address">
    Suite 17<br>
    8 Palfrey Lane<br>
    West Carlow<br>
    Sydney NSW 2156
  </address>

  <ul class="contacts">
    <li>
      <svg viewBox="0 0 24 24" aria-hidden="true"><path d="M6.6 10.8a15.1 15.1 0 0 0 6.6 6.6l2.2-2.2c.3-.3.7-.4 1-.2 1.1.4 2.3.6 3.6.6.6 0 1 .4 1 1V20c0 .6-.4 1-1 1A17 17 0 0 1 3 4c0-.6.4-1 1-1h3.5c.6 0 1 .4 1 1 0 1.3.2 2.5.6 3.6.1.3 0 .7-.2 1z"/></svg>
      02 9561 3048
    </li>
    <li>
      <svg viewBox="0 0 24 24" aria-hidden="true"><path d="M7 1h10a2 2 0 0 1 2 2v18a2 2 0 0 1-2 2H7a2 2 0 0 1-2-2V3a2 2 0 0 1 2-2zm0 3v14h10V4zm5 15.5a1.2 1.2 0 1 0 0 2.4 1.2 1.2 0 0 0 0-2.4z"/></svg>
      0417293086
    </li>
    <li>
      <svg viewBox="0 0 24 24" aria-hidden="true"><path d="M2 5h20v14H2zm2 2v.5l8 5 8-5V7zm0 2.8V17h16V9.8l-8 5z"/></svg>
      simon@harcourtmemorials.com.au
    </li>
    <li>
      <svg viewBox="0 0 24 24" aria-hidden="true"><path d="M12 2a10 10 0 1 0 0 20 10 10 0 0 0 0-20zm6.9 6h-3a15.7 15.7 0 0 0-1.3-3.6A8 8 0 0 1 18.9 8zM12 4c.8 1.2 1.5 2.5 1.9 4h-3.8c.4-1.5 1.1-2.8 1.9-4zM4.3 14a8.3 8.3 0 0 1 0-4h3.4a16.5 16.5 0 0 0 0 4zm.8 2h3a15.7 15.7 0 0 0 1.3 3.6A8 8 0 0 1 5.1 16zm3-8h-3a8 8 0 0 1 4.3-3.6A15.7 15.7 0 0 0 8.1 8zM12 20c-.8-1.2-1.5-2.5-1.9-4h3.8c-.4 1.5-1.1 2.8-1.9 4zm2.3-6H9.7a14.700 14.700 0 0 1 0-4h4.6a14.700 14.700 0 0 1 0 4zm.3 5.6a15.700 15.700 0 0 0 1.3-3.6h3a8 8 0 0 1-4.3 3.6zm1.7-5.6a16.500 16.500 0 0 0 0-4h3.4a8.300 8.300 0 0 1 0 4z"/></svg>
      www.harcourtmemorials.com.au
    </li>
  </ul>
</section>

</body>
</html>
```